Generate website for parcelnook.com

Please design a website for our business. It must be clean, streamlined and obvious.

Our business combines ecommerce, with social networking, and zorvi maps. The logo is a shopping bag (ecommerce) and honeycombs inside representing the various compartments of business that are offered throughout site.

Clients use our site to visit the interior of stores and restaurants through video streaming and can virtually "walk through" the store and purchase items with friends and loved ones through the web.

We want to incorporate this logo with the work that we are doing and play on this honeycomb theme.

Our business is "parcelnook.com" because we are all about "u"!

Please make homepage with about us tab, contact us form, mission tab, we also want a page with our research links included that bolster the case for our startup.

We will incorporate a small video on the front screen. A homepage like fildrawer.com only this time with our parcelnook!

Also include, COMING SOON, on the homepage please.
Updates

These are some good templates/example sites of clean and simple but effective: https://7elmrow.com/preview www.fildrawer.com

We are excited to see your submissions. Currently, a very good and only one designer has posted so far. Let us know!

Please include the TM (trademark) symbol after the logo, the name, and the slogan throughout the website. Thank you!

Put the TM after the LOGO and after the slogan "Placement ran Supreme" Lorcan

Target Market(s)

We will begin with female online shoppers.

Industry/Entity Type

Shopping

Font styles to use
Serif
Sans Serif

Colors
e567a6
fece3e
85cae6

Requirements
Must have
• Clean Look
Simple like Fildrawer with simple options "see film" or login/signup.

With browser tabs at the bottom much like fildrawer.

1. Shopper when opening Parcelnook.com website will see a simple webpage with a large Parcelnook logo in the center.

2. User will see log-in and password or create account in upper right hand corner of webpage. Mobile device website will be underneath logo.

3.We Prefer a background for webpages adding a softer experience on the the eyes of the user. A photo in the background to show shopretail experience.

4. Clicking on theParcelnook logo will inform users of details and instructions about platform. Example: About, contact, mission, Help etc. Logo will become somewhat like an interactive tool for help and guidance.

5. Parcelnook is currently scouting for it's founding venues. A founding venue will be the first venues to appear to the public on the Parcelnook platform. Founding venues (FV) will inherit a lifetime of the lowest possible rates of 2%* for the duration of it's business. All businesses wishing to participate in the founding venues offer please leave your email address and store name and a representative will get back with you.

*Venues will be subjected to credit card and CoinTrail rates in addition.

Nice to have
• http://www.zorvi.com/patents/US5193774

Must include the link above/visual of this page on the site as well.

```html
<!DOCTYPE html>
<html lang="en">
<head>
<meta charset="utf-8">
<title>Parcelnook — Shop and walk with friends through the aisles</title>
<link rel="stylesheet" href="https://fonts.googleapis.com/css2?family=Jost:wght@400;500&family=Arimo:wght@400&display=swap">
<style>
  :root {
    --ink: #111111;
    --wordmark: #5a5a5a;
    --white: #ffffff;
    --band: rgba(255, 255, 255, 0.68);
    --button-top: #ff9f92;
    --button-mid: #f7766a;
    --button-low: #ff8d80;
    --footer: #000000;
    --rule: #6d6d6d;
    --accent: #e567a6;
    --mall-ceiling: #7d6a68;
    --mall-pink: #e9a5b4;
    --mall-wall: #d9cbc8;
    --mall-floor: #6b4d3f;
  }
  * { box-sizing: border-box; margin: 0; padding: 0; }
  html, body { width: 1200px; height: 1091px; overflow: hidden; }
  body { position: relative; background: var(--footer); font-family: "Jost", sans-serif; }

  .hero-backdrop {
    position: absolute; left: 0; top: 0; width: 1200px; height: 745px;
    background:
      radial-gradient(ellipse 260px 200px at 60px 450px, var(--mall-pink), transparent 70%),
      radial-gradient(ellipse 300px 120px at 1000px 720px, #c79a85, transparent 75%),
      linear-gradient(180deg, var(--mall-ceiling) 0%, #a89391 18%, var(--mall-wall) 35%, #cdbab6 70%, var(--mall-floor) 88%, #4e362c 100%);
  }
  .hero-band {
    position: absolute; left: 0; top: 148px; width: 1200px; height: 515px;
    background: var(--band);
  }

  .brand { position: absolute; left: 0; top: 230px; width: 1200px; text-align: center; }
  .brand-mark { display: inline-flex; align-items: center; gap: 18px; }
  .brand-dot { width: 44px; height: 44px; border-radius: 50%; background: var(--accent); }
  .brand-name { font-size: 78px; font-weight: 500; color: var(--wordmark); line-height: 1; }
  .brand-tagline {
    position: absolute; left: 0; top: 336px; width: 1200px; text-align: center;
    font-size: 26px; color: var(--ink);
  }

  .signup-column { position: absolute; top: 396px; width: 380px; text-align: center; }
  .signup-column.shoppers { left: 189px; }
  .signup-column.venues { left: 660px; }
  .signup-heading {
    font-size: 35px; line-height: 53px; color: var(--white); font-weight: 400;
    text-shadow: 1px 2px 4px rgba(0, 0, 0, 0.55);
    height: 106px;
  }
  .signup-box {
    margin-top: 2px; height: 141px; border: 3px solid var(--white); border-radius: 12px;
    background: rgba(255, 255, 255, 0.12);
    padding-top: 10px;
  }
  .email-field {
    display: block; font-size: 22px; color: var(--white);
    text-shadow: 1px 1px 3px rgba(0, 0, 0, 0.55);
  }
  .signup-button {
    display: inline-block; margin-top: 8px; height: 66px; line-height: 60px;
    font-family: "Jost", sans-serif; font-size: 28px; color: var(--white);
    text-shadow: 1px 1px 3px rgba(0, 0, 0, 0.4);
    border: 3px solid var(--white);
    background: linear-gradient(180deg, var(--button-top) 0%, var(--button-mid) 55%, var(--button-low) 100%);
    box-shadow: 3px 4px 5px rgba(0, 0, 0, 0.45);
  }
  .shoppers .signup-button { width: 254px; font-size: 30px; }
  .venues .signup-button { width: 342px; font-size: 27px; letter-spacing: 0.5px; }

  .column-divider {
    position: absolute; left: 617px; top: 398px; width: 2px; height: 240px; background: var(--white);
  }

  .site-footer { position: absolute; left: 0; top: 745px; width: 1200px; height: 346px; font-family: "Arimo", sans-serif; color: var(--white); }
  .footer-nav { position: absolute; left: 90px; top: 22px; width: 170px; list-style: none; text-align: center; }
  .footer-nav li { font-size: 21px; height: 59px; line-height: 24px; }
  .founding-offer {
    position: absolute; left: 0; top: 224px; width: 1244px; text-align: center;
    font-size: 21px; line-height: 33px;
  }
  .footer-rule { position: absolute; left: 63px; top: 292px; width: 1097px; height: 1px; background: var(--rule); }
  .copyright {
    position: absolute; left: 0; top: 304px; width: 1244px; text-align: center;
    font-family: "Jost", sans-serif; font-size: 14px;
  }
</style>
</head>
<body>
  <div class="hero-backdrop" role="img" aria-label="Softly blurred photo of a shopping mall aisle with storefronts"></div>
  <div class="hero-band"></div>

  <header>
    <div class="brand"><span class="brand-mark"><span class="brand-dot"></span><span class="brand-name">Parcelnook</span></span></div>
    <p class="brand-tagline">Shop and walk with friends through the aisles</p>
  </header>

  <main>
    <section class="signup-column shoppers">
      <h2 class="signup-heading">Sign up to join the<br>experience</h2>
      <div class="signup-box">
        <span class="email-field">Enter email adresse</span>
        <span class="signup-button">Enroll here to shop</span>
      </div>
    </section>
    <div class="column-divider"></div>
    <section class="signup-column venues">
      <h2 class="signup-heading">Request or Become a<br>participating store</h2>
      <div class="signup-box">
        <span class="email-field">Enter email adresse</span>
        <span class="signup-button">Enroll or nominate a shop</span>
      </div>
    </section>
  </main>

  <footer class="site-footer">
    <ul class="footer-nav">
      <li>Coming soon</li>
      <li>About us</li>
      <li>mission</li>
      <li>Contact us</li>
    </ul>
    <p class="founding-offer">Founding venues will inherit a 2% lifetime fee*<br>Limited to a select few</p>
    <div class="footer-rule"></div>
    <p class="copyright">©2014 · Parcelnook.com LLC. All rights reserved. Under authorized use of patent #5193774 Patreg</p>
  </footer>
</body>
</html>
```